Residential Remodeling Contractor needs updated business card

I need a new design for my business card.
Name of the company is Ridgefell Construction. I need a card that commands presence, strength, integrity. I have been in business for 28 years. I am a Residential Remodeling Contractor that covers all aspects of a residential remodel and build.

```html
<!DOCTYPE html>
<html lang="en">
<head>
<meta charset="utf-8">
<title>Ridgefell Construction – Business Card</title>
<link rel="stylesheet" href="https://fonts.googleapis.com/css2?family=Cinzel:wght@600&family=Poppins:wght@400&display=swap">
<style>
  :root {
    --backdrop: #b7b7b7;
    --card-blue: #1f3c7c;
    --ink-white: #ffffff;
    --rule: rgba(255, 255, 255, 0.55);
    --shadow: rgba(0, 0, 0, 0.55);
  }
  * { margin: 0; padding: 0; box-sizing: border-box; }
  html, body {
    width: 1200px; height: 1200px; overflow: hidden;
    background: var(--backdrop);
  }
  .stage { position: relative; width: 1200px; height: 1200px; }
  .card {
    position: absolute; top: 303px; height: 594px;
    background: var(--card-blue);
    color: var(--ink-white);
    box-shadow: 4px 4px 4px var(--shadow);
    font-family: "Poppins", sans-serif;
  }
  .card--front { left: 200px; width: 370px; }
  .card--back { left: 599px; width: 364px; }

  .brand {
    position: absolute; left: 0; right: 0;
    display: flex; align-items: center; justify-content: center; gap: 14px;
  }
  .brand__mark { width: 22px; height: 22px; background: var(--ink-white); flex: none; }
  .brand__name {
    font-family: "Cinzel", serif; font-weight: 600;
    color: var(--ink-white); line-height: 1.08; font-size: 30px;
  }
  .card--front .brand { top: 236px; }
  .card--back .brand { top: 120px; }

  .rule { position: absolute; height: 1px; background: var(--rule); }
  .card--front .rule { top: 452px; left: 43px; right: 45px; }

  .tagline {
    position: absolute; top: 468px; left: 0; right: 0;
    text-align: center; font-size: 16.5px; line-height: 21.5px;
  }
  .tagline__lead { font-size: 17.5px; }

  .person { position: absolute; top: 326px; left: 0; right: 0; text-align: center; }
  .person__name { font-family: "Cinzel", serif; font-weight: 600; font-size: 26px; line-height: 30px; }
  .person__role { font-size: 16px; line-height: 18px; }

  .icon-row {
    position: absolute; top: 397px; left: 87px; right: 87px;
    display: flex; align-items: center; gap: 4px;
  }
  .icon-row__line { flex: 1; height: 1px; background: var(--rule); }
  .icon-tile {
    width: 25px; height: 25px; background: var(--ink-white); border-radius: 3px;
    display: flex; align-items: center; justify-content: center;
  }
  .icon-tile svg { width: 17px; height: 17px; }

  .contact {
    position: absolute; top: 428px; left: 0; right: 0;
    text-align: center; font-size: 17px; line-height: 21px;
  }
  .card--back .rule { top: 512px; left: 88px; right: 81px; }
  .address {
    position: absolute; top: 520px; left: 0; right: 0;
    text-align: center; font-size: 16.5px; line-height: 20.5px;
  }
</style>
</head>
<body>
<div class="stage">

  <section class="card card--front">
    <div class="brand">
      <span class="brand__mark"></span>
      <p class="brand__name">Ridgefell<br>Construction</p>
    </div>
    <div class="rule"></div>
    <p class="tagline">
      <span class="tagline__lead">Since 28 years</span><br>
      RESIDENTIAL CONTRACTOR FOR<br>
      REMODELING AND BUILD
    </p>
  </section>

  <section class="card card--back">
    <div class="brand">
      <span class="brand__mark"></span>
      <p class="brand__name">Ridgefell<br>Construction</p>
    </div>

    <div class="person">
      <p class="person__name">Marcus Hale</p>
      <p class="person__role">MANAGING DIRECTOR</p>
    </div>

    <div class="icon-row">
      <span class="icon-row__line"></span>
      <span class="icon-tile" aria-label="Phone">
        <svg viewBox="0 0 24 24"><path fill="#1f3c7c" d="M3 9c0-3 4-5 9-5s9 2 9 5v2h-5V9c-1-1-7-1-8 0v2H3zM6 12h12l2 8H4z"/></svg>
      </span>
      <span class="icon-tile" aria-label="Email">
        <svg viewBox="0 0 24 24"><rect x="2" y="5" width="20" height="14" fill="none" stroke="#1f3c7c" stroke-width="2"/><path d="M2 5l10 8 10-8M2 19l7-7M22 19l-7-7" fill="none" stroke="#1f3c7c" stroke-width="1.6"/></svg>
      </span>
      <span class="icon-tile" aria-label="Website">
        <svg viewBox="0 0 24 24"><circle cx="12" cy="12" r="10" fill="#1f3c7c"/><path d="M6 8c3 0 4 2 3 4s1 4 0 6M14 5c0 3 3 3 5 4M15 14c2 0 3 2 2 4" fill="none" stroke="#fff" stroke-width="1.6"/></svg>
      </span>
      <span class="icon-row__line"></span>
    </div>

    <p class="contact">
      044-123 456 789<br>
      info@webname.com<br>
      www.websitename.com
    </p>

    <div class="rule"></div>
    <p class="address">
      421, Address line goes here<br>
      45452,Country Name
    </p>
  </section>

</div>
</body>
</html>
```